Insert sheet for our Dog Food Package

We need an information sheet to go inn our pet food package, with branding, and information on ingredients, nutrition and feeding guidance. We will also need two additional items which will be a variation on the label design:
1) Label for package (detailed label about us and our food)
2) Label for outer shipping box (simple label for branding)
We will start with the information, insert page. The winning designer will then deliver the package and box labels as simplified versions of the same graphical theme.
I have attached samples of an earlier drafts of the insert piece. Please disregard the style, form and colors of the examples given. THEY ARE ONLY THERE TO SHOW WHAT INFORMATION SHOULD BE INCLUDED. All colors and style should be from our logo (attached). All graphics, font styles, and placement of elements need to be YOUR creative design - not a copy of the sample we gave. PLEASE READ THIS AND PLEASE DO NOT SUBMIT ANY VARIATION OF THE EXAMPLES!!!!!!!

Target Market(s)

Pet Owners

Industry/Entity Type

Pet Food

Colors
EB3D1F
EC4F4E
F09395
F8D3D4
FCEDEE

Requirements
Must have
• All new design. New colors (based in the palette of our logo), new graphics, new fonts, new placement of elements.
Should not have
• Please disregard the style, form and colors of the examples given. THEY ARE ONLY THERE TO SHOW WHAT INFORMATION SHOULD BE INCLUDED.

```html
<!DOCTYPE html>
<html lang="en">
<head>
<meta charset="utf-8">
<title>OLLARIN – Feeding Insert</title>
<link href="https://fonts.googleapis.com/css2?family=Barlow:wght@400;500;600;700&family=Barlow+Semi+Condensed:wght@500;600&display=swap" rel="stylesheet">
<style>
  :root{
    --red:#E63E30;
    --red-deep:#AC2218;
    --pink:#F8D3D4;
    --pink-light:#FCEDEE;
    --pink-mid:#F5B0A5;
    --ink:#1F1A1A;
    --white:#FFFFFF;
  }
  html,body{margin:0;padding:0;width:1200px;height:2172px;overflow:hidden;background:var(--white);}
  .sheet{
    position:relative;width:1241px;height:2246px;
    transform:scale(0.96696);transform-origin:0 0;
    font-family:"Barlow",sans-serif;color:var(--ink);
  }
  .backdrop{position:absolute;inset:0;width:1241px;height:2246px;}
  .card{
    position:absolute;top:620px;width:470px;height:778px;box-sizing:border-box;
    border:2px solid var(--red);border-radius:28px;background:var(--white);
  }
  .card--nutrition{left:72px;}
  .card--feeding{left:699px;}
  .card__banner{
    position:absolute;left:17px;top:17px;width:434px;height:102px;
    background:var(--red);border-radius:10px;color:var(--white);
    font-weight:700;font-size:31px;line-height:42px;text-align:center;
    display:flex;align-items:center;justify-content:center;letter-spacing:0.5px;
  }
  .card__title{
    position:absolute;left:0;right:0;margin:0;text-align:center;
    font-weight:600;font-size:29px;line-height:36px;letter-spacing:0.6px;
  }
  .card--nutrition .card__title{top:138px;}
  .card--feeding .card__title{top:140px;}
  .fact{
    position:absolute;left:17px;width:434px;height:42px;border-radius:9px;
    background:var(--pink);font-weight:700;font-size:23px;
    display:flex;align-items:center;justify-content:center;
  }
  .ingredients{
    position:absolute;left:0;right:0;top:406px;margin:0;
    text-align:center;font-size:23.5px;line-height:37.6px;letter-spacing:0.4px;white-space:nowrap;
  }
  .feed-cell{
    position:absolute;height:57px;border-radius:9px;
    display:flex;align-items:center;justify-content:center;font-size:23.5px;letter-spacing:0.5px;
  }
  .feed-cell--weight{left:17px;width:278px;}
  .feed-cell--meal{left:307px;width:144px;}
  .feed-cell--head{
    background:var(--pink-mid);font-family:"Barlow Semi Condensed",sans-serif;
    font-weight:500;font-size:25px;top:200px;letter-spacing:0;
  }
  .feed-cell--soft{background:var(--pink-light);}
  .feed-cell--tint{background:var(--pink);}
  .footer-box{
    position:absolute;top:1754px;width:414px;height:162px;border-radius:30px;
    background:var(--white);box-sizing:border-box;
  }
  .brand{left:75px;display:flex;align-items:center;justify-content:center;gap:20px;}
  .brand__dot{width:96px;height:96px;border-radius:50%;background:var(--red-deep);flex:none;}
  .brand__name{font-weight:700;font-size:56px;letter-spacing:3px;color:var(--red);}
  .promise{
    left:752px;display:flex;align-items:center;justify-content:center;
    text-align:center;font-size:23.5px;line-height:27.5px;letter-spacing:0.4px;white-space:nowrap;
  }
</style>
</head>
<body>
<div class="sheet">
  <svg class="backdrop" viewBox="0 0 1241 2246" preserveAspectRatio="none" aria-hidden="true">
    <rect width="1241" height="2246" fill="var(--red)"/>
    <path d="M0,505 Q620,225 1241,505 L1241,1540 Q620,1820 0,1540 Z" fill="var(--white)"/>
    <path d="M0,575 Q620,251 1241,555 L1241,620 Q620,290 0,600 Z" fill="var(--red-deep)"/>
    <path d="M0,1432 Q620,1748 1241,1432 L1241,1480 Q620,1750 0,1480 Z" fill="var(--red-deep)"/>
    <rect x="561" y="0" width="119" height="2246" fill="var(--white)"/>
  </svg>

  <section class="card card--nutrition">
    <div class="card__banner">We prepared<br>the best for Shadow</div>
    <h2 class="card__title">NUTRITIONAL INFORMATION</h2>
    <div class="fact" style="top:196px">Protein: 15%</div>
    <div class="fact" style="top:247px">Total Fat: 9.5%</div>
    <div class="fact" style="top:298px">Crude Fiber: 2.0%</div>
    <div class="fact" style="top:349px">Moisture: 72%</div>
    <p class="ingredients">Potassium Citrate, DiCalcium<br>Phosphate, Calcium Carbonate,<br>Garbanzo Beans, Choline Bitartrate,<br>Taurine, Salt, Zinc, Proteinate,<br>Magnesium Oxide, Iron Proteinate,<br>Vitamin B-12, Selenium, Niacin,<br>Riboflavin, Calcium Panthothenate,<br>Thiamine, Vitamin A, Vitamin D<br>Calcium Iodate, Vitamin B6, Folic Acid</p>
  </section>

  <section class="card card--feeding">
    <div class="card__banner">How much should<br>I feed Shadow?</div>
    <h2 class="card__title">RECOMMENDED FEEDING PLAN</h2>
    <div class="feed-cell feed-cell--weight feed-cell--head">APPROXIMATE WEIGHT</div>
    <div class="feed-cell feed-cell--meal feed-cell--head">FULL MEAL</div>

    <div class="feed-cell feed-cell--weight feed-cell--soft" style="top:270px">&lt;20 lbs</div>
    <div class="feed-cell feed-cell--meal feed-cell--soft" style="top:270px">110 g</div>
    <div class="feed-cell feed-cell--weight feed-cell--tint" style="top:341px">20-29 lbs</div>
    <div class="feed-cell feed-cell--meal feed-cell--tint" style="top:341px">200 g</div>
    <div class="feed-cell feed-cell--weight feed-cell--tint" style="top:412px">30-39 lbs</div>
    <div class="feed-cell feed-cell--meal feed-cell--tint" style="top:412px">250 g</div>
    <div class="feed-cell feed-cell--weight feed-cell--tint" style="top:483px">40-54 lbs</div>
    <div class="feed-cell feed-cell--meal feed-cell--tint" style="top:483px">300 g</div>
    <div class="feed-cell feed-cell--weight feed-cell--soft" style="top:554px">55-69 lbs</div>
    <div class="feed-cell feed-cell--meal feed-cell--soft" style="top:554px">350 g</div>
    <div class="feed-cell feed-cell--weight feed-cell--soft" style="top:625px">70-85 lbs</div>
    <div class="feed-cell feed-cell--meal feed-cell--soft" style="top:625px">400 g</div>
    <div class="feed-cell feed-cell--weight feed-cell--tint" style="top:696px">85+ lbs</div>
    <div class="feed-cell feed-cell--meal feed-cell--tint" style="top:696px">500 g</div>
  </section>

  <div class="footer-box brand">
    <span class="brand__dot"></span>
    <span class="brand__name">OLLARIN</span>
  </div>

  <div class="footer-box promise">We Revolutionized the industry.<br>Not Formulated to meet a<br>minimum standard, but to<br>develop the maximum health<br>of the whole dog.</div>
</div>
</body>
</html>
```